Designing a website that functions as the shop window for the various aspects of my business -...

I need a website, with separate webpages covering the different components of my practice (small animal consultancy, equine behaviour consultancy, legal case work and education provider). I have a website (www.petcalmstudio.ie) but I haven't updated it in recent years to reflect the newer developments / aspects of my business. Most of my work has been in Ireland but I would like to begin to create an international profile, particularly with regard to the legal casework and offering education within the international horse industry. My overall goal is to improve understanding of animals and animal behaviour, and by doing so, help to reduce the performance of behaviour problems, and also improve animal welfare as a result.

Target Market(s)

Horse and dog owners, horse riders, veterinary surgeons, solicitors

Industry/Entity Type

Legal

Logo Text

Text to be decided on

Number of Pages Required

5+ page

Font styles to use
Sans Serif
Decorative
Script

Colors

Designer to choose colors to be used in the design.

Requirements
Must have
• Relevant content from the attached Flyer including photos
• Use of the phrases:
• 'Understanding Animals'
• Improving animals lives through better understanding
• Science-based, up-to-date relevant information regarding animal behaviour
Nice to have
• 'Leading professional service educating people in understanding animals'
• Separate pages for 1) About, 2) Canine and Feline behaviour Consultancy 3) Equine Consultancy 4) Legal expert witness Consultancy 5) Education 6, FAQs
Should not have
• Prices of services (as these may change from time to time)

```html
<!DOCTYPE html>
<html lang="en">
<head>
<meta charset="utf-8">
<title>Pet Calm Studio</title>
<link href="https://fonts.googleapis.com/css2?family=Montserrat:wght@400;500;600;700&family=Open+Sans:wght@400;600&display=swap" rel="stylesheet">
<style>
:root{
  --green:#1a7f4b;
  --green-dark:#146a3e;
  --mint:#e3f2ec;
  --grey-band:#e6e6e6;
  --text:#444;
  --footer:#2b2b2b;
  --white:#fff;
}
*{box-sizing:border-box;margin:0;padding:0}
html,body{width:1200px;height:3495px;overflow:hidden}
body{position:relative;font-family:"Open Sans",sans-serif;color:var(--text);background:var(--white)}
.abs{position:absolute}
.header{top:0;left:0;width:1200px;height:82px;background:#f4f4f4}
.brand{left:145px;top:20px;display:flex;align-items:center;gap:12px}
.brand-mark{width:34px;height:34px;background:var(--green)}
.brand-name{font-family:"Montserrat",sans-serif;font-weight:600;font-size:26px;color:var(--green)}
.contact{right:290px;top:30px;font-size:14px;color:#555;display:flex;align-items:center;gap:6px}
.login{left:983px;top:22px;width:72px;height:36px;border:1.5px solid var(--green);color:var(--green);font-size:14px;display:flex;align-items:center;justify-content:center;font-family:"Montserrat",sans-serif}
.nav{top:82px;left:0;width:1200px;height:32px;background:var(--green);display:flex;align-items:center;padding-left:145px;gap:24px}
.nav a{color:var(--white);text-decoration:none;font-family:"Montserrat",sans-serif;font-size:11.5px;font-weight:500;text-transform:uppercase}
.nav a.active{color:#cfe9d9}
.hero{top:114px;left:0;width:1200px;height:501px;background:linear-gradient(90deg,#2e3b1e 0%,#7a5a2c 35%,#c08a45 50%,#6a5226 70%,#24321a 100%)}
.hero-text{right:145px;top:185px;width:380px;text-align:right;color:var(--white);font-family:"Montserrat",sans-serif;font-size:24px;line-height:33px}
.arrow-circle{width:38px;height:38px;border-radius:50%;background:var(--white);display:flex;align-items:center;justify-content:center}
h2{font-family:"Montserrat",sans-serif;font-weight:500;color:var(--green);font-size:29px}
.welcome-title{left:145px;top:688px}
.welcome-text{left:145px;top:740px;width:535px;font-size:11.5px;line-height:19px}
.welcome-text p+p{margin-top:18px}
.btn{background:var(--green);color:var(--white);font-family:"Montserrat",sans-serif;font-size:12px;display:flex;align-items:center;justify-content:center}
.read-more{left:145px;top:1010px;width:88px;height:35px}
.green-block{left:995px;top:843px;width:205px;height:202px;background:var(--green)}
.welcome-photo{left:715px;top:700px;width:340px;height:203px;background:linear-gradient(135deg,#1a1a1a,#3b3f46 55%,#6f87a8 70%,#222)}
.grey-band{top:1120px;left:0;width:1200px;height:315px;background:var(--grey-band)}
.center-title{left:0;width:1200px;text-align:center}
.practice{width:296px}
.practice-photo{height:192px}
.practice-label{height:70px;background:var(--green);color:var(--white);font-family:"Montserrat",sans-serif;font-size:16px;line-height:22px;display:flex;align-items:center;justify-content:center;text-align:center;padding:0 20px}
.offer{width:217px;text-align:center}
.offer-photo{height:157px}
.offer-caption{margin-top:18px;color:var(--green);font-family:"Montserrat",sans-serif;font-size:16px;line-height:22px}
.dog-band{top:1915px;left:0;width:1200px;height:400px;background:linear-gradient(180deg,#5a4630 0%,#8c6d4a 45%,#a07c55 100%)}
.understanding{left:320px;top:2245px;width:560px;height:143px;background:var(--green);text-align:center;color:var(--white);font-family:"Montserrat",sans-serif}
.understanding h3{font-weight:500;font-size:28px;margin-top:12px}
.understanding p{font-size:19px;margin-top:6px}
.contact-btn{margin:14px auto 0;width:88px;height:35px;background:#1e1e1e;color:var(--white);font-size:12px;display:flex;align-items:center;justify-content:center}
.story{width:296px}
.story-card{height:256px;background:var(--mint);text-align:center;padding:16px 24px 0;font-size:13.5px;line-height:22px;position:relative}
.story-card::after{content:"";position:absolute;left:50%;bottom:-12px;margin-left:-12px;border:12px solid transparent;border-bottom:0;border-top-color:var(--mint)}
.story-name{margin-top:30px;text-align:center;font-family:"Montserrat",sans-serif;font-size:16px;color:#333}
.stars{display:flex;justify-content:center;gap:3px;margin-top:6px}
.chev{color:#888}
.map{top:2910px;left:0;width:1200px;height:440px;background:linear-gradient(135deg,#d9d9d9,#eeeeee 50%,#d2d2d2)}
.map-label{left:220px;top:2948px;font-size:15px;color:#333}
.footer{top:3350px;left:0;width:1200px;height:145px;background:var(--footer);text-align:center;color:#ccc;font-size:11px}
.footer-links{margin-top:30px}
.footer-links a{color:#ccc;text-decoration:none;margin:0 8px}
.footer-copy{margin-top:12px;color:#999}
.socials{display:flex;justify-content:center;gap:10px;margin-top:16px}
.socials span{width:24px;height:24px;border-radius:50%}
</style>
</head>
<body>

<header class="abs header">
  <div class="abs brand"><span class="brand-mark"></span><span class="brand-name">Pet Calm Studio</span></div>
  <div class="abs contact">
    <svg width="14" height="14" viewBox="0 0 24 24"><path fill="#1a7f4b" d="M6.6 10.8a15 15 0 006.6 6.6l2.2-2.2c.3-.3.7-.4 1-.2 1.1.4 2.3.6 3.6.6.6 0 1 .4 1 1V20c0 .6-.4 1-1 1A17 17 0 013 4c0-.6.4-1 1-1h3.5c.6 0 1 .4 1 1 0 1.3.2 2.5.6 3.6.1.3 0 .7-.2 1z"/></svg>
    <strong style="color:#333">087 555 0142</strong>&nbsp; Mon-Fri from 9.30 am until 6.00pm
  </div>
  <div class="abs login">&#8594;&nbsp;Login</div>
</header>

<nav class="abs nav">
  <a class="active" href="#">Home</a><a href="#">About</a><a href="#">Canine and Feline Behaviour Consultancy</a><a href="#">Equine Consultancy</a><a href="#">Legal Expert Witness Consultancy</a><a href="#">Education</a><a href="#">Contact Us</a>
</nav>

<section class="abs hero" role="img" aria-label="Photo of a golden retriever balancing a stack of colourful dog biscuits on its nose"></section>
<p class="abs hero-text">Science-based, up-to-date relevant information regarding animal behaviour</p>
<div class="abs arrow-circle" style="left:54px;top:346px"><svg width="14" height="14" viewBox="0 0 14 14"><path d="M9 2L4 7l5 5" stroke="#222" stroke-width="2.5" fill="none"/></svg></div>
<div class="abs arrow-circle" style="left:1106px;top:346px"><svg width="14" height="14" viewBox="0 0 14 14"><path d="M5 2l5 5-5 5" stroke="#222" stroke-width="2.5" fill="none"/></svg></div>

<h2 class="abs welcome-title">Welcome to Pet Calm Studio</h2>
<div class="abs welcome-text">
  <p>Animals have been used by humans for a variety of purposes, including as a source of food, for hunting, for mobility, to help win battles, for sport - and most recently, for companionship. Whether we are dog or cat lovers, horseriders or owners, through the course of our relationship with our animals, many of us will be faced with problem behaviours, such as aggression, excessive barking, destructiveness (dogs), spraying, fear problems, aggression (cats), bucking, refusing to load into trailers, rearing, shying (horses).</p>
  <p>So why do problems arise? In investigating and treating behaviour problems, many factors need to be taken into account, including the animal's breeding (what genetic makeup the animal has inherited from it's parents), health, previous experience, normal behaviour patterns of that species (dogs will display very different normal behaviours to cats, or to horses) and motivational factors (what things are important to that species...</p>
</div>
<a class="abs btn read-more">Read More</a>
<div class="abs green-block"></div>
<div class="abs welcome-photo" role="img" aria-label="Photo of a lecture with slides projected in a darkened room"></div>

<div class="abs grey-band"></div>
<h2 class="abs center-title" style="top:1190px">Our Practices</h2>
<div class="abs practice" style="left:145px;top:1243px"><div class="practice-photo" role="img" aria-label="Photo of a small white puppy on a wooden floor" style="background:linear-gradient(180deg,#a89a8a,#6f6254)"></div><div class="practice-label">Small Animal Consultancy</div></div>
<div class="abs practice" style="left:452px;top:1243px"><div class="practice-photo" role="img" aria-label="Photo of a woman cuddling her dog" style="background:linear-gradient(135deg,#2a2a2a,#8a7a6c 60%,#d0c8c0)"></div><div class="practice-label">Equine Behaviour Consultancy</div></div>
<div class="abs practice" style="left:760px;top:1243px"><div class="practice-photo" role="img" aria-label="Photo of a woman sitting on a beach with her dog at sunset" style="background:linear-gradient(180deg,#c9b4a2,#a58c74 55%,#7a6652)"></div><div class="practice-label">Legal Case Work and Education Provider</div></div>

<h2 class="abs center-title" style="top:1576px">What We Offer</h2>
<div class="abs offer" style="left:145px;top:1628px"><div class="offer-photo" role="img" aria-label="Photo of a scruffy terrier" style="background:linear-gradient(135deg,#4a3e32,#9a8a74)"></div><div class="offer-caption">Behaviour consultations</div></div>
<div class="abs offer" style="left:376px;top:1628px"><div class="offer-photo" role="img" aria-label="Photo of dogs in a training session" style="background:linear-gradient(135deg,#8a8478,#2c2a28)"></div><div class="offer-caption">Training sessions</div></div>
<div class="abs offer" style="left:607px;top:1628px"><div class="offer-photo" role="img" aria-label="Photo of a horse being led in an indoor arena" style="background:linear-gradient(180deg,#5a3e2a,#9a6a44)"></div><div class="offer-caption">Training your horse - theory and practice</div></div>
<div class="abs offer" style="left:838px;top:1628px"><div class="offer-photo" role="img" aria-label="Photo of a horse and a dog in a green field" style="background:linear-gradient(180deg,#6a8a4a,#3a5a2a)"></div><div class="offer-caption">Training, performance and welfare</div></div>

<section class="abs dog-band" role="img" aria-label="Photo of a row of dogs of different breeds sitting on a dirt path"></section>
<div class="abs understanding">
  <h3>Understanding Animals</h3>
  <p>Improving animals lives through better understanding</p>
  <div class="contact-btn">Contact Us</div>
</div>

<h2 class="abs center-title" style="top:2460px">Success Stories</h2>
<svg class="abs" style="left:52px;top:2626px" width="20" height="28" viewBox="0 0 20 28"><path d="M15 3L5 14l10 11" stroke="#888" stroke-width="2.5" fill="none"/></svg>
<svg class="abs" style="left:1126px;top:2626px" width="20" height="28" viewBox="0 0 20 28"><path d="M5 3l10 11L5 25" stroke="#888" stroke-width="2.5" fill="none"/></svg>

<div class="abs story" style="left:145px;top:2512px">
  <div class="story-card"><svg width="40" height="30" viewBox="0 0 40 30"><path fill="#8fcfae" d="M2 16h8l-4 12h6l4-12V2H2zM22 16h8l-4 12h6l4-12V2H22z"/></svg><p style="margin-top:10px">Vivamus eleifend vitae nulla vel malesuada. In ac malesuada lacus, et consectetur ante. Fusce vitae lectus sit amet mi pulvinar maximus. Aenean placerat, nibh vel accumsan aliquet, magna nibh accumsan nibh, ac tempus nunc ipsum ac tellus. Cras augue magna.</p></div>
  <div class="story-name">Liam Dorsey</div>
  <div class="stars"><svg width="96" height="16" viewBox="0 0 96 16"><g fill="#1a7f4b"><path id="s" d="M8 0l2.4 5 5.6.6-4.2 3.8 1.2 5.6L8 12.2 3 15l1.2-5.6L0 5.6 5.6 5z"/><use href="#s" x="20"/><use href="#s" x="40"/><use href="#s" x="60"/><use href="#s" x="80"/></g></svg></div>
</div>
<div class="abs story" style="left:452px;top:2512px">
  <div class="story-card"><svg width="40" height="30" viewBox="0 0 40 30"><path fill="#8fcfae" d="M2 16h8l-4 12h6l4-12V2H2zM22 16h8l-4 12h6l4-12V2H22z"/></svg><p style="margin-top:10px">Aenean faucibus lacus ut mollis commodo. Donec vestibulum odio sem, ac laoreet massa ullamcorper id. Donec molestie nisl et tellus hendrerit vehicula. Nunc eu ligula sed quam pulvinar maximus in vitae eros. Proin porta fermentum ipsum, vel porttitor.</p></div>
  <div class="story-name">Emily</div>
  <div class="stars"><svg width="96" height="16" viewBox="0 0 96 16"><g fill="#1a7f4b"><use href="#s"/><use href="#s" x="20"/><use href="#s" x="40"/><use href="#s" x="60"/><use href="#s" x="80"/></g></svg></div>
</div>
<div class="abs story" style="left:760px;top:2512px">
  <div class="story-card"><svg width="40" height="30" viewBox="0 0 40 30"><path fill="#8fcfae" d="M2 16h8l-4 12h6l4-12V2H2zM22 16h8l-4 12h6l4-12V2H22z"/></svg><p style="margin-top:10px">Praesent elementum nulla sit amet justo pellentesque scelerisque. Nam et tortor in ante iaculis porttitor in luctus mi. Vivamus gravida sem a pretium euismod. Nam lobortis, purus et fringilla tempus, risus eros dignissim diam, eget finibus sem risus sit amet eros.</p></div>
  <div class="story-name">William</div>
  <div class="stars"><svg width="96" height="16" viewBox="0 0 96 16"><g fill="#1a7f4b"><use href="#s"/><use href="#s" x="20"/><use href="#s" x="40"/><use href="#s" x="60"/><use href="#s" x="80"/></g></svg></div>
</div>

<section class="abs map" role="img" aria-label="Grey street map of the city showing the clinic location"></section>
<p class="abs map-label">24 Building name, Street name, City Zipcode</p>
<svg class="abs" style="left:366px;top:2972px" width="18" height="26" viewBox="0 0 18 26"><path fill="#1a7f4b" d="M9 0a9 9 0 019 9c0 7-9 17-9 17S0 16 0 9a9 9 0 019-9z"/><circle cx="9" cy="9" r="3.5" fill="#fff"/></svg>

<footer class="abs footer">
  <div class="footer-links"><a href="#">Home</a>|<a href="#">About</a>|<a href="#">Canine and Feline behaviour Consultancy</a>|<a href="#">Equine Consultancy</a>|<a href="#">Legal expert witness Consultancy</a>|<a href="#">Education</a>|<a href="#">Contact us</a></div>
  <div class="footer-copy">Copyright &copy; 2019 Pet Calm Studio. All rights reserved.</div>
  <div class="socials"><span style="background:#3b5998"></span><span style="background:#1da1f2"></span><span style="background:#e52d27"></span><span style="background:#5b7fa6"></span></div>
</footer>

</body>
</html>
```